Create a cover for English Grammar Workbook

This book describes a system to learn English in a proper way - we call it The ''Lantern Row'' System.

It focuses on not only teaching grammar and its structures, but also giving students tips on how to use it and the best ways to remember what they learn.

The cover should have 3 realistic pillars (3D), with one closer to the front to show that this book is the 1st (front) Pillar.

The title is: "Building Sentences That Stick: *A Friendly Path Through Usage"*

Author's name: Doreen Calloway

```html
<!DOCTYPE html>
<html lang="en">
<head>
<meta charset="utf-8">
<title>Building Sentences That Stick — Cover</title>
<link rel="stylesheet" href="https://fonts.googleapis.com/css2?family=Allura&family=Cinzel:wght@500;700&family=Montserrat:wght@600&display=swap">
<style>
  :root {
    --page-bg: #f1f1f1;
    --cover-bg: #3b3b3c;
    --brand-red: #d3121c;
    --title-white: #ffffff;
    --title-grey: #c9c9c9;
    --pillar-light: #e6e6e6;
    --pillar-mid: #9e9e9e;
  }
  * { box-sizing: border-box; margin: 0; padding: 0; }
  html, body {
    width: 1200px; height: 800px; overflow: hidden;
    background: var(--page-bg);
  }
  .page {
    width: 1200px; height: 800px;
    display: flex; align-items: center; justify-content: center;
  }
  .cover {
    position: relative;
    width: 500px; height: 730px;
    background: var(--cover-bg);
    overflow: hidden;
  }
  .subtitle-frame {
    position: absolute; left: 41px; top: 16px;
    width: 413px; height: 37px;
    border: 3px solid var(--brand-red);
    display: flex; align-items: center; justify-content: center;
    font-family: "Montserrat", sans-serif; font-weight: 600;
    font-size: 16px; letter-spacing: 1px; text-transform: uppercase;
    color: var(--title-white);
  }
  .title-script {
    position: absolute; left: 0; right: 0; top: 92px;
    text-align: center;
    font-family: "Allura", cursive;
    font-size: 66px; line-height: 1;
    color: var(--title-white);
    z-index: 2;
  }
  .title-band {
    position: absolute; left: 46px; width: 413px;
    background: var(--brand-red);
    display: flex; align-items: center; justify-content: center;
    font-family: "Cinzel", serif; font-weight: 700;
    color: var(--title-white); letter-spacing: 2px;
  }
  .title-band--first { top: 149px; height: 74px; font-size: 52px; }
  .title-band--second { top: 223px; height: 66px; font-size: 62px; letter-spacing: 6px; }
  .title-grey {
    position: absolute; left: 0; right: 0; top: 300px;
    text-align: center;
    font-family: "Cinzel", serif; font-weight: 700;
    font-size: 52px; line-height: 1; letter-spacing: 5px;
    color: var(--title-grey);
  }
  .pillars-art {
    position: absolute; left: 50px; top: 365px;
    width: 400px; height: 311px;
    background:
      radial-gradient(ellipse 22% 50% at 50% 55%, var(--pillar-light) 0%, rgba(230,230,230,0.55) 60%, transparent 100%),
      radial-gradient(ellipse 16% 38% at 16% 66%, rgba(220,220,220,0.8) 0%, transparent 100%),
      radial-gradient(ellipse 16% 40% at 84% 64%, rgba(220,220,220,0.8) 0%, transparent 100%),
      linear-gradient(to bottom, transparent 0%, rgba(158,158,158,0.15) 100%);
  }
  .author-band {
    position: absolute; left: 0; right: 0; bottom: 0;
    height: 54px;
    background: var(--brand-red);
    display: flex; align-items: center; justify-content: center;
    font-family: "Cinzel", serif; font-weight: 700;
    font-size: 23px; letter-spacing: 6px;
    color: var(--title-white);
  }
</style>
</head>
<body>
  <main class="page">
    <section class="cover">
      <div class="subtitle-frame">A Friendly Path Through Usage</div>
      <h1 class="book-title">
        <span class="title-script">Building</span>
        <span class="title-band title-band--first">SENTENCES</span>
        <span class="title-band title-band--second">THAT</span>
        <span class="title-grey">STICK</span>
      </h1>
      <div class="pillars-art" role="img" aria-label="Three white classical Ionic columns, the tall middle one standing in front of two shorter ones"></div>
      <div class="author-band">DOREEN CALLOWAY</div>
    </section>
  </main>
</body>
</html>
```